Namibia currently imports 60% of its food. Harvest Crest Oruva is an initiative which will assist Namibia to become self sustainable in terms of food production. We aim to do this through the development of 3 agricultural production zones which will include farming zones, local farmer assistance, processing and distribution of the final products. Please see our project overview attached.

```html
<!DOCTYPE html>
<html lang="en">
<head>
<meta charset="utf-8">
<title>Harvest Crest Oruva</title>
<link rel="stylesheet" href="https://fonts.googleapis.com/css2?family=Lora:wght@500;600;700&family=Roboto:wght@400;500;700&display=swap">
<style>
:root{
  --green-dark:#0b3d1f;
  --green:#0e6a36;
  --green-deep:#08542a;
  --brown:#c49262;
  --brown-band:#c38a52;
  --text:#6d6d6d;
  --ink:#1d1d1d;
  --grey-bg:#f3f3f3;
  --white:#ffffff;
}
*{box-sizing:border-box;margin:0;padding:0}
html,body{width:1200px;height:3981px;overflow:hidden;background:var(--white)}
body{position:relative;font-family:"Roboto",sans-serif;color:var(--text)}
.abs{position:absolute}
.serif{font-family:"Lora",serif}

/* header */
.brand{position:absolute;font-family:"Lora",serif;font-weight:500;color:var(--green);font-size:25px;letter-spacing:.5px;white-space:nowrap}
.nav{position:absolute;top:43px;left:604px;display:flex;gap:28px;font-size:14px;font-weight:700;color:var(--ink);z-index:3}
.drop{position:absolute;left:617px;top:12px;z-index:3}
.join{position:absolute;left:951px;top:31px;width:136px;height:43px;border-radius:22px;background:var(--brown);color:#fff;font-weight:700;font-size:14px;display:flex;align-items:center;justify-content:center;z-index:3}

/* hero */
.hero-photo{position:absolute;left:0;top:0;width:1200px;height:690px;
  background:linear-gradient(180deg,#ffffff 0%,#fff8e6 18%,#f7dfa4 27%,#e3b865 32%,#7d9a38 38%,#4f8424 48%,#3c6d1c 62%,#5b7a26 74%,#3f6a1e 88%,#2f5a18 100%)}
.hero-curve{position:absolute;left:0;top:480px;z-index:2}
.hero-title{position:absolute;left:0;width:1200px;text-align:center;z-index:2}
.welcome{top:128px;font-family:"Lora",serif;font-size:17px;color:#a06b36;letter-spacing:.5px}
.hero-name{top:155px;font-family:"Lora",serif;font-weight:600;font-size:56px;color:var(--green-dark);letter-spacing:1px}
.hero-sub{top:228px;font-family:"Lora",serif;font-weight:600;font-size:37px;color:var(--green-dark);letter-spacing:8px}

/* buttons */
.btn{position:absolute;height:42px;border-radius:22px;display:flex;align-items:center;justify-content:center;gap:8px;color:#fff;font-weight:700;font-size:14px;z-index:2;white-space:nowrap}
.btn-dark{background:var(--green-dark)}
.btn-brown{background:var(--brown)}
.btn svg{display:block}

/* round photos */
.photo{position:absolute;width:364px;height:364px}
.photo .ring{position:absolute;left:14px;top:0;width:364px;height:364px;border-radius:50%;background:var(--green-dark)}
.photo .pic{position:absolute;left:0;top:0;width:364px;height:364px;border-radius:50%}

/* section text */
.heading{position:absolute;font-family:"Lora",serif;font-weight:600;font-size:40px;line-height:45px;color:var(--green-dark)}
.bar{position:absolute;width:59px;height:4px;background:var(--brown)}
.para{position:absolute;font-size:14px;line-height:25.8px;text-align:justify;color:var(--text)}
.subhead{position:absolute;font-weight:500;font-size:20px;color:var(--ink)}

/* quote */
.quote-band{position:absolute;left:0;top:1654px;width:1200px;height:426px}
.quote{position:absolute;left:0;top:1750px;width:1200px;text-align:center;font-family:"Lora",serif;font-weight:600;font-size:40px;line-height:50px;color:#fff}

/* aim */
.aim-bg{position:absolute;left:0;top:2594px;width:1200px;height:580px;background:var(--grey-bg)}
.aim-item{position:absolute;display:flex;align-items:center;gap:14px;font-size:14px;font-weight:500;line-height:19px;color:var(--ink)}
.aim-item.right{text-align:right}
.aim-divider{position:absolute;left:345px;top:2768px;width:1px;height:350px;background:#d9d9d9}
.aim-rule{position:absolute;height:1px;background:#e0e0e0}
.person{position:absolute;left:690px;top:2644px;width:310px;height:530px;border-radius:150px 150px 0 0;background:linear-gradient(180deg,#6b4a2e 0%,#8a4f38 35%,#b25c42 55%,#d9a53c 80%,#c9922e 100%)}

/* project */
.project-bg{position:absolute;left:0;top:3174px;width:1200px;height:485px;background:linear-gradient(180deg,#c88e54,#bb8248)}
.project .heading,.project .para{color:#fff}
.project .bar{background:#fff}

/* footer */
.foot-nav{position:absolute;top:3803px;left:450px;display:flex;gap:27px;font-size:14px;font-weight:700;color:var(--ink)}
.subscribe{position:absolute;left:357px;top:3856px;width:481px;height:48px;border-radius:24px;background:#f2f2f2;display:flex;align-items:center;padding-left:24px;font-size:14px;color:#777}
.subscribe .go{position:absolute;right:0;top:1px;width:46px;height:46px;border-radius:50%;background:var(--green-dark);display:flex;align-items:center;justify-content:center}
.foot-rule{position:absolute;left:111px;top:3931px;width:977px;height:1px;background:#d4d4d4}
.copyright{position:absolute;left:0;top:3950px;width:1200px;text-align:center;font-size:12px;color:#444}
</style>
</head>
<body>

<!-- Hero -->
<div class="hero-photo" role="img" aria-label="Sunlit field of green potato crop rows stretching to the horizon"></div>
<svg class="hero-curve" width="1200" height="220" viewBox="0 480 1200 220">
  <path d="M0,636 C120,690 380,690 773,578 C960,530 1100,560 1200,602 L1200,700 L0,700 Z" fill="#ffffff"/>
  <path d="M0,630 C120,682 380,684 773,570 C960,522 1100,552 1200,596" fill="none" stroke="#0e5a2e" stroke-width="7"/>
</svg>

<div class="brand" style="left:111px;top:36px;">HARVEST CREST ORUVA</div>
<svg class="drop" width="16" height="24" viewBox="0 0 16 24"><path d="M8,1 C5,8 1,12 1,16 a7,7 0 0 0 14,0 C15,12 11,8 8,1 Z" fill="#2b8fd6"/></svg>
<nav class="nav"><span>Home</span><span>About</span><span>Our Project</span><span>Contact</span></nav>
<div class="join">JOIN US</div>

<div class="hero-title welcome">WELCOME TO</div>
<div class="hero-title hero-name">HARVEST CREST</div>
<div class="hero-title hero-sub">ORUVA</div>
<div class="btn btn-dark" style="left:513px;top:287px;width:173px;">GET ATARTED
  <svg width="13" height="13" viewBox="0 0 14 14"><circle cx="7" cy="7" r="7" fill="#fff"/><path d="M5.5,4 L8.5,7 L5.5,10" stroke="#0b3d1f" stroke-width="2" fill="none"/></svg></div>

<!-- About -->
<div class="photo" style="left:179px;top:725px;">
  <div class="ring"></div>
  <div class="pic" role="img" aria-label="Farmer in an apron carrying a crate of fresh vegetables" style="background:linear-gradient(160deg,#c9d3d9 0%,#8c9aa3 35%,#4a4f52 60%,#7c8a4a 85%,#5d6e36 100%)"></div>
</div>
<h2 class="heading" style="left:646px;top:738px;">ABOUT US</h2>
<div class="bar" style="left:646px;top:786px;"></div>
<p class="para" style="left:646px;top:808px;width:375px;">Namibia is a young democracy in Sub-Saharan Africa with a population of approximately 2.5 Million people. The country's agricultural sector has been slow to keep up with the increasing population. As a consequence,approximately 60% of the foodrequired to feed the nation is imported. The elevated cost of these imported foods means a large proportion of the population consume food with low nutritional value.</p>
<div class="btn btn-dark" style="left:647px;top:1028px;width:174px;">VIEW MORE
  <svg width="13" height="13" viewBox="0 0 14 14"><circle cx="7" cy="7" r="7" fill="#fff"/><path d="M5.5,4 L8.5,7 L5.5,10" stroke="#0b3d1f" stroke-width="2" fill="none"/></svg></div>

<!-- Solution -->
<h2 class="heading" style="left:179px;top:1210px;">HARVEST CREST<br>SOLUTION</h2>
<div class="bar" style="left:180px;top:1308px;"></div>
<p class="para" style="left:180px;top:1331px;width:375px;">The long term intention of the Harvest Crest Oruva program would be to establish 3 distinct food production and processing zones which have access to large amounts of arable land, with high quality soil and strong water resources, as well as good transport connections to relevant markets.</p>
<div class="btn btn-dark" style="left:180px;top:1500px;width:174px;">VIEW MORE
  <svg width="13" height="13" viewBox="0 0 14 14"><circle cx="7" cy="7" r="7" fill="#fff"/><path d="M5.5,4 L8.5,7 L5.5,10" stroke="#0b3d1f" stroke-width="2" fill="none"/></svg></div>
<div class="photo" style="left:629px;top:1197px;">
  <div class="ring"></div>
  <div class="pic" role="img" aria-label="Smiling older farmer in a checked shirt holding a tablet among green plants" style="background:linear-gradient(150deg,#3f6b2a 0%,#5f8d3b 40%,#4f79a6 62%,#5a8c3a 85%,#355f22 100%)"></div>
</div>

<!-- Quote -->
<svg class="quote-band" width="1200" height="426" viewBox="0 0 1200 426">
  <defs><linearGradient id="bandGrad" x1="0" y1="0" x2="0" y2="1"><stop offset="0" stop-color="#0e6a36"/><stop offset="1" stop-color="#07542a"/></linearGradient></defs>
  <path d="M0,0 L1200,8 L1200,403 L0,426 Z" fill="url(#bandGrad)"/>
</svg>
<div class="quote">GIVE A MAN A FISH AND FEED HIM FOR<br>A DAY, TEACH A MAN &nbsp;TO FISHAND<br>FEED HIM FOR A LIFETIME</div>
<div class="btn btn-brown" style="left:513px;top:1926px;width:174px;">GET STARTED
  <svg width="13" height="13" viewBox="0 0 14 14"><circle cx="7" cy="7" r="7" fill="#fff"/><path d="M5.5,4 L8.5,7 L5.5,10" stroke="#c49262" stroke-width="2" fill="none"/></svg></div>

<!-- Sustainability -->
<div class="photo" style="left:179px;top:2148px;">
  <div class="ring"></div>
  <div class="pic" role="img" aria-label="Freshly harvested potatoes on soil in front of green crop rows" style="background:linear-gradient(180deg,#e8eef0 0%,#4f8a2c 22%,#3d7a22 48%,#7a5a3a 62%,#c9a77a 80%,#4a3826 100%)"></div>
</div>
<h2 class="heading" style="left:646px;top:2162px;">HARVEST CREST<br>SUSTAINABILITY</h2>
<div class="bar" style="left:647px;top:2253px;"></div>
<h3 class="subhead" style="left:646px;top:2283px;">Processing Facilities</h3>
<p class="para" style="left:646px;top:2321px;width:375px;">Each of the allocated production zones will be furnished with handling, processing and milling facilities for all crops produced as part of the program. These will include Potatoes, Maize and Wheat.</p>
<div class="btn btn-dark" style="left:647px;top:2452px;width:174px;">VIEW MORE
  <svg width="13" height="13" viewBox="0 0 14 14"><circle cx="7" cy="7" r="7" fill="#fff"/><path d="M5.5,4 L8.5,7 L5.5,10" stroke="#0b3d1f" stroke-width="2" fill="none"/></svg></div>

<!-- Our aim -->
<div class="aim-bg"></div>
<h2 class="heading" style="left:179px;top:2673px;">OUR AIM</h2>
<div class="bar" style="left:180px;top:2727px;"></div>
<div class="aim-divider"></div>
<div class="aim-rule" style="left:240px;top:2840px;width:95px;"></div>
<div class="aim-rule" style="left:240px;top:2935px;width:95px;"></div>
<div class="aim-rule" style="left:240px;top:3030px;width:95px;"></div>

<div class="aim-item" style="left:179px;top:2770px;"><svg width="48" height="48" viewBox="0 0 48 48"><circle cx="24" cy="24" r="20" fill="none" stroke="#c49262" stroke-width="2"/><circle cx="24" cy="24" r="10" fill="none" stroke="#2f2f2f" stroke-width="2"/></svg><span>Farm<br>Management</span></div>
<div class="aim-item" style="left:179px;top:2866px;"><svg width="48" height="48" viewBox="0 0 48 48"><path d="M10,40 L10,22 M38,40 L38,22 M24,30 L24,10" stroke="#c49262" stroke-width="2" fill="none"/><path d="M18,30 C18,20 30,20 30,30" stroke="#2f2f2f" stroke-width="2" fill="none"/></svg><span>Crop<br>Management</span></div>
<div class="aim-item" style="left:179px;top:2961px;"><svg width="48" height="48" viewBox="0 0 48 48"><rect x="6" y="24" width="36" height="16" rx="2" fill="none" stroke="#2f2f2f" stroke-width="2"/><path d="M24,24 L24,10" stroke="#c49262" stroke-width="2"/></svg><span>Soil Health<br>and Irrigation</span></div>
<div class="aim-item" style="left:179px;top:3056px;"><svg width="48" height="48" viewBox="0 0 48 48"><circle cx="24" cy="16" r="7" fill="none" stroke="#c49262" stroke-width="2"/><path d="M8,42 C8,30 40,30 40,42" stroke="#c49262" stroke-width="2" fill="none"/></svg><span>Business<br>Management</span></div>

<div class="aim-item right" style="left:365px;top:2770px;width:150px;justify-content:flex-end;"><span>Marketing</span><svg width="48" height="48" viewBox="0 0 48 48"><path d="M10,20 L30,10 L30,38 L10,28 Z" fill="none" stroke="#c49262" stroke-width="2"/><path d="M36,18 L42,14 M36,30 L42,34" stroke="#2f2f2f" stroke-width="2"/></svg></div>
<div class="aim-item right" style="left:365px;top:2866px;width:150px;justify-content:flex-end;"><span>Computer<br>Skills</span><svg width="48" height="48" viewBox="0 0 48 48"><rect x="6" y="8" width="36" height="26" rx="2" fill="none" stroke="#2f2f2f" stroke-width="2"/><path d="M16,40 L32,40 M14,28 L14,22 M22,28 L22,16 M30,28 L30,20" stroke="#2f2f2f" stroke-width="2"/></svg></div>
<div class="aim-item right" style="left:365px;top:2961px;width:150px;justify-content:flex-end;"><span>Logistics<br>Management</span><svg width="48" height="48" viewBox="0 0 48 48"><rect x="8" y="8" width="18" height="14" fill="none" stroke="#c49262" stroke-width="2"/><path d="M8,38 L22,38 C30,38 34,30 42,30" stroke="#c49262" stroke-width="2" fill="none"/></svg></div>
<div class="aim-item right" style="left:365px;top:3056px;width:150px;justify-content:flex-end;"><span>Vehicle<br>Mechanics</span><svg width="48" height="48" viewBox="0 0 48 48"><circle cx="24" cy="24" r="18" fill="none" stroke="#2f2f2f" stroke-width="3" stroke-dasharray="6 3"/><circle cx="24" cy="24" r="8" fill="none" stroke="#2f2f2f" stroke-width="2"/></svg></div>

<div class="person" role="img" aria-label="Smiling farmer in a bucket hat and plaid shirt standing with arms crossed"></div>

<!-- Project -->
<div class="project-bg" role="img" aria-label="Warm brown field texture"></div>
<div class="project">
  <div class="photo" style="left:179px;top:3236px;">
    <div class="ring"></div>
    <div class="pic" role="img" aria-label="Irrigation sprinkler over a young maize field under a blue sky" style="background:linear-gradient(180deg,#7fb6e6 0%,#cfe3f3 35%,#8aa06a 50%,#3f7a26 70%,#2f6a1c 100%)"></div>
  </div>
  <h2 class="heading" style="left:646px;top:3250px;">OUR PROJECT</h2>
  <div class="bar" style="left:647px;top:3306px;"></div>
  <p class="para" style="left:646px;top:3335px;width:375px;">Each of the allocated production zones will be furnished with handling, processing and milling facilities for all crops produced as part of the program. These will include Potatoes, Maize and Wheat.</p>
  <p class="para" style="left:646px;top:3448px;width:375px;">Each of the allocated production zones will be furnished with handling, processing and milling</p>
  <div class="btn btn-dark" style="left:647px;top:3523px;width:174px;">VIEW MORE
    <svg width="13" height="13" viewBox="0 0 14 14"><circle cx="7" cy="7" r="7" fill="#fff"/><path d="M5.5,4 L8.5,7 L5.5,10" stroke="#0b3d1f" stroke-width="2" fill="none"/></svg></div>
</div>

<!-- Footer -->
<div class="brand" style="left:0;width:1200px;text-align:center;top:3732px;">HARVEST CREST ORUVA</div>
<nav class="foot-nav"><span>Home</span><span>About</span><span>Our Project</span><span>Contact</span></nav>
<div class="subscribe">Enter &nbsp;Email Address
  <div class="go"><svg width="14" height="16" viewBox="0 0 14 16"><path d="M4,2 L10,8 L4,14" stroke="#fff" stroke-width="2.4" fill="none"/></svg></div>
</div>
<div class="foot-rule"></div>
<div class="copyright">Copyright@2024 All Rights By Harvest Crest Oruva</div>

</body>
</html>
```